Email Banner (LoomDigest)

We require an email banner for our email promotions sent to prospect clients. The banner needs to contain the wording LoomDigest and use the same colour scheme as the logos attached.

This is for B2B professional's so needs to look like a place you would come to read technology articles.

```html
<!DOCTYPE html>
<html lang="en">
<head>
<meta charset="utf-8">
<title>LoomDigest Email Banner</title>
<link rel="stylesheet" href="https://fonts.googleapis.com/css2?family=Outfit:wght@500;700&display=swap">
<style>
  :root {
    --navy: #031024;
    --white: #ffffff;
    --page: #ececec;
    --green: #7bc043;
    --teal: #2aa6a4;
    --blue: #0096d6;
  }
  * { margin: 0; padding: 0; box-sizing: border-box; }
  html, body {
    width: 1200px;
    height: 512px;
    overflow: hidden;
    background: var(--page);
  }
  .banner {
    position: absolute;
    left: 30px;
    top: 125px;
    width: 1140px;
    height: 262px;
    background: var(--white);
    overflow: hidden;
    font-family: "Outfit", sans-serif;
  }
  .contact-band {
    position: absolute;
    left: 0;
    top: 0;
    width: 1140px;
    height: 262px;
  }
  .brand {
    position: absolute;
    left: 49px;
    top: 44px;
    display: flex;
    align-items: center;
    gap: 26px;
  }
  .brand-square {
    width: 22px;
    height: 22px;
    background: var(--blue);
  }
  .brand-name {
    font-weight: 500;
    font-size: 90px;
    line-height: 1;
    letter-spacing: -1px;
    color: var(--navy);
  }
  .contact {
    position: absolute;
    top: 191px;
    left: 49px;
    display: flex;
    align-items: center;
    color: var(--white);
    font-weight: 700;
    font-size: 27px;
    line-height: 1;
  }
  .contact-item {
    display: flex;
    align-items: center;
    gap: 11px;
  }
  .contact-item + .contact-item { margin-left: 30px; }
  .contact-icon { width: 22px; height: 22px; flex: none; }
  .phone-number { letter-spacing: 0.5px; }
  .web-address { letter-spacing: 4px; font-weight: 500; }
</style>
</head>
<body>
  <div class="banner">
    <svg class="contact-band" viewBox="0 0 1140 262" aria-hidden="true">
      <polygon points="0,163 861,163 754,262 0,262" fill="var(--navy)"/>
    </svg>

    <div class="brand">
      <span class="brand-square"></span>
      <span class="brand-name">LoomDigest.io</span>
    </div>

    <div class="contact">
      <div class="contact-item">
        <svg class="contact-icon" viewBox="0 0 24 24" aria-hidden="true">
          <circle cx="12" cy="12" r="12" fill="var(--green)"/>
          <path d="M8.2 6.2c.4-.3.9-.2 1.2.2l1.2 1.9c.2.4.2.8-.1 1.1l-.8.8c.6 1.4 1.7 2.5 3.1 3.1l.8-.8c.3-.3.7-.3 1.1-.1l1.9 1.2c.4.3.5.8.2 1.2l-.8 1c-.4.5-1.1.7-1.7.5-3.4-1.1-6-3.7-7.1-7.1-.2-.6 0-1.3.5-1.7z" fill="var(--white)"/>
        </svg>
        <span class="phone-number">555 0142 0199</span>
      </div>
      <div class="contact-item">
        <svg class="contact-icon" viewBox="0 0 24 24" aria-hidden="true">
          <g fill="none" stroke="var(--green)" stroke-width="2">
            <circle cx="12" cy="12" r="10"/>
            <ellipse cx="12" cy="12" rx="4.5" ry="10"/>
            <line x1="2" y1="12" x2="22" y2="12"/>
            <line x1="4" y1="7" x2="20" y2="7"/>
            <line x1="4" y1="17" x2="20" y2="17"/>
          </g>
        </svg>
        <span class="web-address">www.loomdigest.io</span>
      </div>
    </div>
  </div>
</body>
</html>
```